Natural Light/Organic/Documentary Photography Business

I like a simple, approachable, feminine, earthy/organic feel. Earth/neutral tones, nothing too loud or obnoxious. I like the watercolor look. I don't want anything too trendy or something I'll get tired of after a couple months. As far as colors, I am much more a fan of cream/taupe/blue/green...not a fan of pink or purple at all.

Target Market(s)

Weddings & Families

Industry/Entity Type

Wedding Photography

Contact Information for Business Card

website, email, phone number

Font styles to use
Other font styles liked:
• Horizontes, Gotham

Colors

Designer to choose colors to be used in the design.

Requirements
Must have
• Website: www.mirelhatchway.com
• Phone: 418.629.5073
• Email: mirel@mirelhatchway.com
Nice to have
• I like the watercolor look but its not necessary. I like simple/earthy tones. Nothing too loud or distracting. Simple & feminine without being too girly. I like an approachable/soft feel.
• Instagram: www.instagram.com/mirelhatchwayphotography/
Should not have
• NO loud colors or design or pattern. I do not want a photo of a camera or lens or anything cheesy like that.

```html
<!DOCTYPE html>
<html lang="en">
<head>
<meta charset="utf-8">
<title>Mirel Hatchway Photography – Business Card</title>
<link rel="stylesheet" href="https://fonts.googleapis.com/css2?family=Montserrat:wght@300;400;500&display=swap">
<style>
  :root {
    --page: #f4f2ef;
    --card: #ffffff;
    --wash-deep: #b9aa9b;
    --wash-mid: #cfc3b6;
    --wash-light: #e6ddd3;
    --wash-pale: #f3efea;
    --frame: #a79b90;
    --ink: #8a7d72;
    --ink-soft: #a2958a;
    --label: #7d736b;
  }
  * { margin: 0; padding: 0; box-sizing: border-box; }
  html, body {
    width: 1200px;
    height: 867px;
    overflow: hidden;
    background: var(--page);
    font-family: "Montserrat", Arial, sans-serif;
  }
  .business-card {
    position: absolute;
    left: 100px;
    top: 127px;
    width: 1000px;
    height: 613px;
    background: var(--card);
  }
  .watercolor-wash {
    position: absolute;
    left: 70px;
    top: 64px;
    width: 858px;
    height: 483px;
    display: block;
  }
  .info-panel {
    position: absolute;
    left: 182px;
    top: 163px;
    width: 634px;
    height: 287px;
    background: var(--card);
    border: 1px solid var(--frame);
    text-align: center;
  }
  .brand-name {
    margin-top: 44px;
    font-size: 42px;
    font-weight: 300;
    letter-spacing: 0.04em;
    color: var(--ink);
    line-height: 1.1;
  }
  .brand-tagline {
    margin-top: 10px;
    font-size: 11.5px;
    font-weight: 400;
    letter-spacing: 0.45em;
    padding-left: 0.45em;
    color: var(--ink-soft);
  }
  .contact-list {
    list-style: none;
    margin-top: 46px;
    font-size: 13.5px;
    line-height: 24px;
    color: var(--ink-soft);
    font-weight: 300;
  }
  .contact-label {
    font-weight: 500;
    color: var(--label);
  }
  .contact-divider { margin: 0 4px; }
  .contact-dot { margin: 0 9px; }
</style>
</head>
<body>
  <main class="business-card">
    <svg class="watercolor-wash" viewBox="0 0 858 483" preserveAspectRatio="none" role="img" aria-label="Soft taupe and cream watercolor wash behind the contact panel">
      <defs>
        <linearGradient id="wash-gradient" x1="0" y1="0" x2="1" y2="1">
          <stop offset="0" stop-color="var(--wash-mid)"/>
          <stop offset="0.35" stop-color="var(--wash-deep)"/>
          <stop offset="0.7" stop-color="var(--wash-light)"/>
          <stop offset="1" stop-color="var(--wash-pale)"/>
        </linearGradient>
      </defs>
      <rect width="858" height="483" fill="url(#wash-gradient)"/>
    </svg>

    <section class="info-panel">
      <h1 class="brand-name">Mirel Hatchway</h1>
      <p class="brand-tagline">PHOTOGRAPHY</p>
      <ul class="contact-list">
        <li><span class="contact-label">Website</span><span class="contact-divider">|</span>www.mirelhatchway.com<span class="contact-dot">·</span><span class="contact-label">Phone</span><span class="contact-divider">|</span>418 629 5073</li>
        <li><span class="contact-label">Email</span><span class="contact-divider">|</span>mirel@mirelhatchway.com</li>
        <li><span class="contact-label">Instagram</span><span class="contact-divider">|</span>@mirelhatchwayphotography</li>
      </ul>
    </section>
  </main>
</body>
</html>
```